EB-5 Regional Center needs a Web design

Harlow Ridge Financial Partners is an expanding EB-r regional center. We have been successful in sponsoring multiple projects of third-party developers and placing EB-5, B-1, and Private Investments into multiple projects.

We are now partnering directly with project developers in the energy and healthcare to raise foreign capital for projects in those industries. The foreign capital is used as project equity and our collective balance sheets are used to guarantee debt to complete the funding of the projects.

We need a web site where we can post our company credentials, the bios of each partner, a document page for each of our projects where we can post specific project related documents which foreign investors can read, and we will need a section where foreign investors can fill out investor forms confirming that they are qualified investors and leaving their contact so that our agents and executives can make contact.

The final design should reflect the exceptional experience of the partners and our financial strength and stability.

We do have a logo we would want to use on the web design.

Target Market(s)

EB-5 Investors, B-1 Investors, Private Equity and other investors seeking quality investment in job creating US projects.

Coding

Number of Pages Required

5+ page

Font styles to use
Sans Serif

Requirements
Must have
• Pages to display company info, partner bios, projects completed, and a projects in-process page where we can post documents and info on projects for which we are seeking foreign investment. We also need a section where investors can enter their qualifying personal information and leave contact information for us.

```html
<!DOCTYPE html>
<html lang="en">
<head>
<meta charset="utf-8">
<title>Harlow Ridge Financial Partners</title>
<link rel="stylesheet" href="https://fonts.googleapis.com/css2?family=Raleway:wght@500;600;700&family=Roboto:wght@400;500;700&display=swap">
<style>
:root{
  --blue:#2a5ea9;
  --ink:#1b1b1b;
  --text:#555;
  --gray-band:#eeeeee;
  --light:#f3f3f4;
  --white:#fff;
}
*{margin:0;padding:0;box-sizing:border-box}
html,body{width:1200px;height:4468px;overflow:hidden}
body{position:relative;font-family:Roboto,sans-serif;color:var(--ink);background:var(--white)}
.abs{position:absolute}
.heading{font-family:Raleway,sans-serif;font-weight:600;font-size:38px;color:var(--ink);text-align:center;position:absolute;left:0;width:1200px}
.btn{position:absolute;background:var(--blue);color:#fff;font-family:Raleway,sans-serif;font-weight:700;font-size:19px;display:flex;align-items:center;justify-content:center}

.topbar{top:0;left:0;width:1200px;height:42px;background:#000;color:#fff;font-size:17px}
.topbar .mail{left:88px;top:10px}

.header{top:42px;left:0;width:1200px;height:126px;background:#fff}
.phone-lbl{left:134px;top:40px;font-size:17px}
.phone-num{left:134px;top:62px;font-size:22px;font-weight:700}
.brand{left:366px;top:32px;display:flex;align-items:center;gap:14px}
.brand .mark{width:50px;height:50px;background:#8a8c90}
.brand .name{font-family:Raleway,sans-serif;font-weight:700;font-size:30px;color:#6f7175;line-height:1.05}
.search{left:839px;top:41px;width:266px;height:47px;border:1.5px solid #bbb;border-radius:24px;font-size:17px;color:#444;padding:14px 0 0 16px}
.search .go{position:absolute;right:5px;top:5px;width:36px;height:36px}

.nav{top:168px;left:0;width:1200px;height:61px;background:var(--gray-band);border-top:1px solid #ddd;border-bottom:1px solid #ddd}
.nav a{position:absolute;top:20px;font-weight:500;font-size:18px;color:#111;text-decoration:none}
.nav a.on{color:var(--blue)}

.hero{top:229px;left:0;width:1200px;height:583px;background:linear-gradient(120deg,#5a7ba8 0%,#2d4f85 45%,#1d3566 75%,#3f6299 100%)}
.hero h1{position:absolute;top:190px;left:0;width:1200px;text-align:center;font-family:Raleway,sans-serif;font-weight:600;font-size:46px;color:#fff}
.hero p{position:absolute;top:256px;left:220px;width:760px;text-align:center;font-size:19px;line-height:32px;color:#f0f0f0}

.about-img{left:0;top:903px;width:477px;height:392px;border-radius:0 40px 40px 0;background:linear-gradient(135deg,#e6e9ee,#b8bec8 50%,#4a4f58)}
.about h2{position:absolute;left:588px;top:895px;font-family:Raleway,sans-serif;font-weight:600;font-size:40px}
.about p{position:absolute;left:588px;top:970px;width:520px;font-size:16px;line-height:36px;color:var(--text);text-align:justify}

.projects{top:1390px;left:0;width:1200px;height:609px;background:linear-gradient(180deg,#18191d,#0f1013)}
.projects .heading{color:#fff}
.card-img{top:124px;height:225px}
.card-title{top:372px;font-family:Raleway,sans-serif;font-weight:600;font-size:22px;color:#fff}
.card-text{top:412px;width:320px;font-size:13.5px;line-height:27px;color:#ddd;text-align:justify}
.card-more{top:520px;font-size:14.5px;font-weight:500;color:#fff}
.dot{top:570px;width:14px;height:14px;border:2px solid #fff;border-radius:50%}

.bio{width:296px;height:296px;border-radius:50%;background:radial-gradient(circle at 50% 40%,#8e8e8e,#2b2b2b 70%,#111)}
.bio-name{top:2490px;width:360px;text-align:center;font-family:Raleway,sans-serif;font-weight:500;font-size:22px}
.bio-role{top:2527px;width:360px;text-align:center;font-size:14px;font-weight:500;color:#444}
.bio-hover{display:flex;align-items:center;justify-content:center;text-align:center;color:#fff;font-size:16px;font-weight:500;line-height:27px;padding:0 22px}

.blog{top:2636px;left:0;width:1200px;height:641px;background:var(--light)}
.post-img{top:133px;width:320px;height:233px}
.post-meta{top:378px;width:320px;font-size:14.5px;color:#333;display:flex;justify-content:space-between}
.post-title{top:413px;font-family:Raleway,sans-serif;font-weight:500;font-size:21px}
.post-text{top:450px;width:320px;font-size:14.5px;line-height:29px;color:#555;text-align:justify}
.post-more{top:576px;font-size:16px;font-weight:700}

.field{border:1.5px solid #c9c9c9;background:#fff;font-size:18px;color:#333;padding:20px 0 0 15px}

.footer{top:4053px;left:0;width:1200px;height:415px;background:linear-gradient(180deg,#1c1d21,#111215)}
.footer .brandname{left:88px;top:92px;font-family:Raleway,sans-serif;font-weight:700;font-size:30px;color:#fff;display:flex;align-items:center;gap:12px}
.footer .brandname i{width:44px;height:44px;background:#fff;display:block}
.footer .about-f{left:88px;top:150px;width:320px;font-size:18.5px;line-height:36px;color:#fff;text-align:justify}
.footer h4{position:absolute;top:82px;font-family:Raleway,sans-serif;font-weight:600;font-size:21px;color:#fff}
.footer ul{position:absolute;top:120px;list-style:none;font-size:17.5px;line-height:36px;color:#fff}
.footer .copy{left:0;top:364px;width:1200px;text-align:center;font-size:15.5px;color:#ddd}
</style>
</head>
<body>

<div class="abs topbar">
  <span class="abs mail">info@harlowridgefinancial.com</span>
</div>

<div class="abs header">
  <svg class="abs" style="left:88px;top:46px" width="36" height="36" viewBox="0 0 36 36" aria-hidden="true">
    <circle cx="18" cy="18" r="16" fill="none" stroke="#333" stroke-width="2"/>
    <path d="M12 10c1-1 3-1 4 1l1 3c0 1-1 2-2 2 1 3 3 5 6 6 0-1 1-2 2-2l3 1c2 1 2 3 1 4-3 3-8 0-12-4s-6-8-3-11z" fill="#333"/>
  </svg>
  <span class="abs phone-lbl">Contact us:</span>
  <span class="abs phone-num">(555) 014-2290</span>
  <div class="abs brand">
    <span class="mark"></span>
    <span class="name">Harlow Ridge<br><span style="font-size:19px;letter-spacing:2px">Financial Partners</span></span>
  </div>
  <div class="abs search">Search
    <svg class="go" viewBox="0 0 36 36" aria-hidden="true"><circle cx="18" cy="18" r="18" fill="#2a5ea9"/><circle cx="16.5" cy="16.5" r="6" fill="none" stroke="#fff" stroke-width="2.4"/><path d="M21 21l5 5" stroke="#fff" stroke-width="2.6"/></svg>
  </div>
</div>

<nav class="abs nav">
  <a class="on" style="left:198px">HOME</a>
  <a style="left:305px">ABOUT US</a>
  <a style="left:452px">PROJECT</a>
  <a style="left:590px">BLOG</a>
  <a style="left:699px">PARTNER BIOS</a>
  <a style="left:887px">CONTACT US</a>
</nav>

<section class="abs hero">
  <div class="abs" style="left:0;top:0;width:1200px;height:583px" role="img" aria-label="Businessman in a suit behind financial data figures and a rising bar chart"></div>
  <h1>HARLOW RIDGE FINANCIAL PARTNERS</h1>
  <p>Sed ut perspiciatis unde omnis iste natus error sit voluptatem accusantium doloremque laudantium, totam rem aperiam, eaque ipsa quae ab illo</p>
  <span class="btn" style="left:518px;top:343px;width:164px;height:52px">GET STARTED</span>
</section>

<section class="about">
  <div class="abs about-img" role="img" aria-label="Business partners shaking hands in a bright office"></div>
  <h2>ABOUT US</h2>
  <p>Sed ut perspiciatis unde omnis iste natus error sit voluptatem accusantium doloremque laudantium, totam rem aperiam, eaque ipsa quae ab illo inventore veritatis et quasi architecto beatae vitae dicta sunt explicabo. Nemo enim ipsam voluptatem quia voluptas sit aspernatur aut odit aut fugit, sed quia consequuntur magni dolores eos qui ratione voluptatem sequi nesciunt. Neque porro quisquam est, qui dolorem ipsum quia dolor sit amet, consectetur</p>
  <span class="btn" style="left:584px;top:1243px;width:148px;height:52px">READ MORE</span>
</section>

<section class="abs projects">
  <h2 class="heading" style="top:42px">LATEST PROJECTS</h2>
  <div class="abs card-img" style="left:92px;width:326px;background:linear-gradient(135deg,#e9edf3,#9fb0c8)" role="img" aria-label="Laptop with financial charts and reports"></div>
  <div class="abs card-img" style="left:442px;width:325px;background:linear-gradient(135deg,#e8e6e2,#6f747c)" role="img" aria-label="Team meeting around a presentation board"></div>
  <div class="abs card-img" style="left:787px;width:321px;background:linear-gradient(135deg,#dfe3e8,#8c96a6)" role="img" aria-label="Hands reviewing charts with a calculator"></div>

  <span class="abs card-title" style="left:92px">FINIBUS BONORUM</span>
  <span class="abs card-title" style="left:443px">ACCUSAMUS ET IUSTO</span>
  <span class="abs card-title" style="left:784px">MOLESTIAS EXCEPTURI</span>

  <p class="abs card-text" style="left:92px">Lorem ipsum dolor sit amet, consectetur adipiscing elit, sed do eiusmod tempor incididunt ut labore et dolore magna aliqua.</p>
  <p class="abs card-text" style="left:443px">Lorem ipsum dolor sit amet, consectetur adipiscing elit, sed do eiusmod tempor incididunt ut labore et dolore magna aliqua.</p>
  <p class="abs card-text" style="left:784px">Lorem ipsum dolor sit amet, consectetur adipiscing elit, sed do eiusmod tempor incididunt ut labore et dolore magna aliqua.</p>

  <span class="abs card-more" style="left:91px">READ MORE</span>
  <span class="abs card-more" style="left:440px">READ MORE</span>
  <span class="abs card-more" style="left:783px">READ MORE</span>

  <span class="abs dot" style="left:559px"></span>
  <span class="abs dot" style="left:580px;background:#fff"></span>
  <span class="abs dot" style="left:600px"></span>
</section>

<section>
  <h2 class="heading" style="top:2085px">PARTNER BIOS</h2>
  <div class="abs bio" style="left:91px;top:2176px" role="img" aria-label="Black and white portrait of a partner"></div>
  <div class="abs bio bio-hover" style="left:452px;top:2176px;box-shadow:0 6px 14px rgba(0,0,0,.35)" role="img" aria-label="Black and white portrait of the managing partner">Sed ut perspiciatis unde omnis iste natus error sit voluptatem accusantium doloremque laudantium</div>
  <div class="abs bio" style="left:812px;top:2176px" role="img" aria-label="Black and white portrait of a partner"></div>

  <span class="abs bio-name" style="left:59px">MARCUS ELLERY</span>
  <span class="abs bio-name" style="left:428px">DANIEL OKORO</span>
  <span class="abs bio-name" style="left:789px">PETER LANSING</span>
  <span class="abs bio-role" style="left:59px">MANGER</span>
  <span class="abs bio-role" style="left:428px">MANAGING PARTNER</span>
  <span class="abs bio-role" style="left:786px">PARTNER</span>
</section>

<section class="abs blog">
  <h2 class="heading" style="top:49px">LASTEST BLOG</h2>
  <div class="abs post-img" style="left:92px;background:linear-gradient(135deg,#c9bfb2,#6c5a48)" role="img" aria-label="Hands with a pen over financial paperwork"></div>
  <div class="abs post-img" style="left:442px;background:linear-gradient(135deg,#b79a78,#5a4a3a)" role="img" aria-label="Pen pointing at a chart on a wooden desk"></div>
  <div class="abs post-img" style="left:792px;background:linear-gradient(135deg,#1b2a44,#2f7bd0)" role="img" aria-label="Businessman holding a glowing digital tablet"></div>

  <div class="abs post-meta" style="left:92px"><span>▦ JAN 31, 2020</span><span>● HRF</span></div>
  <div class="abs post-meta" style="left:442px"><span>▦ JAN 31, 2020</span><span>● HRF</span></div>
  <div class="abs post-meta" style="left:792px"><span>▦ JAN 31, 2020</span><span>● HRF</span></div>

  <span class="abs post-title" style="left:91px">FINIBUS BONORUM</span>
  <span class="abs post-title" style="left:442px">FINIBUS BONORUM</span>
  <span class="abs post-title" style="left:792px">FINIBUS BONORUM</span>

  <p class="abs post-text" style="left:91px">Lorem ipsum dolor sit amet, consectetur adipiscing elit, sed dao eiusmod tempor incididunt ut labore et dolore magna aliqua. Ut enim ad minim veniam,</p>
  <p class="abs post-text" style="left:442px">Lorem ipsum dolor sit amet, consectetur adipiscing elit, sed do eiusmod tempor incididunt ut laboAre et dolore magna aliqua. Ut enim ad minim veniam.</p>
  <p class="abs post-text" style="left:792px">Lorem ipsum dolor sit amet, consectetur adipiscing elit, sed do eiusmod tempor incididunt ut laboAre et dolore magna aliqua. Ut enim ad minim veniam.</p>

  <span class="abs post-more" style="left:90px">READ MORE</span>
  <span class="abs post-more" style="left:440px">READ MORE</span>
  <span class="abs post-more" style="left:792px">READ MORE</span>
</section>

<section>
  <h2 class="heading" style="top:3362px">CONTACT US</h2>
  <div class="abs field" style="left:88px;top:3470px;width:502px;height:59px">Name</div>
  <div class="abs field" style="left:607px;top:3470px;width:503px;height:59px">Email</div>
  <div class="abs field" style="left:88px;top:3546px;width:502px;height:59px">Phone number</div>
  <div class="abs field" style="left:607px;top:3546px;width:503px;height:59px">Address</div>
  <div class="abs field" style="left:88px;top:3622px;width:1022px;height:229px">Messages</div>
  <span class="btn" style="left:487px;top:3898px;width:219px;height:71px;font-size:24px;font-weight:600">SUBMIT</span>
</section>

<footer class="abs footer">
  <div class="abs brandname"><i></i>Harlow Ridge</div>
  <p class="abs about-f">This is Photoshop's version of Lorem Ipsum. Proin gravida nibh vel velit auctor aliquet. Aenean sollicitudin, lorem quis bibendum auctor, nisi elit</p>
  <h4 style="left:508px">QUICKS LINKS</h4>
  <ul style="left:508px"><li>Home</li><li>About Us</li><li>Project</li><li>Blog</li><li>Partner Bios</li><li>Contact Us</li></ul>
  <h4 style="left:714px">CONTACT US</h4>
  <ul style="left:714px"><li>412 Alder Crest Road</li><li>Brookfield, GA 30999</li><li>555 014 2290</li><li>info@hrfp.com</li></ul>
  <h4 style="left:950px">FOLLOW US</h4>
  <ul style="left:950px"><li>Fanpage</li><li>Chirpline</li><li>Proflink</li></ul>
  <p class="abs copy">Copyright 2020 Harlow Ridge Financial Partners | All Rights Reserved</p>
</footer>

</body>
</html>
```